Bramblewood Joinery Website

My client Bramblewood Joinery is looking for a redesign for a Word Press Website. Their current site is at www.bramblewoodjoinery.example They are a custom cabinet company, but also create bathroom, living room, bar and entertainment and bedroom cabinets too. They would like a design that emulates the master craftsman work they do yet a contemporary style.

Their current site was designed using Flash elements.

Target Market(s)

Home owners and builders of high end homes

Industry/Entity Type

Entertainment

Font styles to use
Serif
Decorative

Requirements
Must have
• Must show their work and logo using a contemporary style.
Nice to have
• Sliders that showcase their projects.

```html
<!DOCTYPE html>
<html lang="en">
<head>
<meta charset="utf-8">
<title>Bramblewood Joinery</title>
<link rel="stylesheet" href="https://fonts.googleapis.com/css2?family=Open+Sans:wght@400;600&family=Lora:wght@400&family=Pinyon+Script&display=swap">
<style>
  :root {
    --green: #3f9a3a;
    --green-dark: #2f7d2c;
    --nav: #3b3b3b;
    --nav-line: #555555;
    --ink: #2b2b2b;
    --muted: #6a6a6a;
    --rule: #e2e2e2;
    --footer: #2a2a2a;
    --footer-text: #d8d8d8;
    --white: #ffffff;
    --wood-dark: #4a4440;
    --wood-light: #cfc8c0;
  }
  * { box-sizing: border-box; margin: 0; padding: 0; }
  html, body { width: 882px; height: 1200px; overflow: hidden; background: var(--white); }
  body { font-family: "Open Sans", Arial, sans-serif; color: var(--ink); position: relative; }

  .site-header { position: absolute; top: 0; left: 0; width: 882px; height: 98px; }
  .brand { position: absolute; left: 88px; top: 26px; display: flex; align-items: center; gap: 10px; }
  .brand-dot { width: 40px; height: 40px; border-radius: 50%; background: var(--green); }
  .brand-name { font-size: 17px; font-weight: 600; color: var(--green-dark); }
  .tagline { position: absolute; right: 88px; top: 20px; text-align: right; font-family: "Pinyon Script", cursive; color: var(--green); font-size: 22px; line-height: 26px; }

  .main-nav { position: absolute; top: 98px; left: 0; width: 882px; height: 36px; background: var(--nav); }
  .main-nav ul { list-style: none; display: flex; margin-left: 88px; height: 36px; }
  .main-nav li { font-size: 11px; color: var(--white); padding: 0 13px; line-height: 36px; border-right: 1px solid var(--nav-line); }
  .main-nav li.active { background: var(--green); padding: 0 18px; }

  .slider { position: absolute; top: 146px; left: 88px; width: 706px; height: 296px; }
  .slide-main { position: absolute; left: 0; top: 0; width: 529px; height: 296px; background: linear-gradient(135deg, var(--wood-dark) 0%, #8c8580 45%, var(--wood-light) 100%); }
  .slide-caption { position: absolute; left: 22px; bottom: 26px; font-family: "Lora", Georgia, serif; color: var(--white); font-size: 24px; }
  .slide-arrow { position: absolute; top: 136px; }
  .slide-arrow.prev { left: 8px; }
  .slide-arrow.next { right: 8px; }
  .slide-thumbs { position: absolute; left: 537px; top: 0; width: 169px; }
  .slide-thumb { height: 93px; margin-bottom: 8.5px; background: linear-gradient(160deg, #6e6862, #d7d1ca); }

  .section-title { position: absolute; left: 0; width: 882px; text-align: center; font-weight: 400; font-size: 26px; color: var(--ink); }
  .welcome-title { top: 478px; }
  .welcome-text { position: absolute; top: 528px; left: 120px; width: 642px; text-align: center; font-size: 10px; line-height: 16px; color: var(--muted); }
  .btn { position: absolute; height: 24px; background: var(--green); color: var(--white); font-size: 10px; line-height: 24px; text-align: center; border-radius: 2px; }
  .btn-read { top: 594px; left: 403px; width: 76px; }

  .rule { position: absolute; left: 88px; width: 706px; height: 1px; background: var(--rule); }
  .rule-one { top: 640px; }
  .rule-two { top: 852px; }

  .offer-title { position: absolute; top: 656px; left: 120px; width: 642px; text-align: center; font-size: 20px; line-height: 28px; color: var(--ink); }
  .gallery { position: absolute; top: 728px; left: 88px; width: 706px; display: flex; gap: 20px; }
  .gallery-item { width: 125px; height: 96px; background: linear-gradient(150deg, var(--wood-dark), #a49d96 70%, var(--wood-light)); }

  .video-title { top: 868px; }
  .video-intro { position: absolute; top: 918px; left: 88px; width: 420px; }
  .video-intro h3 { font-size: 13px; font-weight: 400; color: var(--green); margin-bottom: 8px; }
  .video-intro p { font-size: 10px; line-height: 16px; color: var(--muted); }
  .btn-view { top: 1022px; left: 88px; width: 76px; }
  .video-frame { position: absolute; top: 908px; left: 530px; width: 264px; height: 160px; background: linear-gradient(140deg, #3f3a36, #9a928a 60%, #d9d2ca); }
  .play-icon { position: absolute; left: 110px; top: 58px; }

  .site-footer { position: absolute; top: 1100px; left: 0; width: 882px; height: 100px; background: var(--footer); }
  .footer-links { position: absolute; top: 20px; left: 88px; width: 440px; font-size: 10px; line-height: 18px; color: var(--footer-text); }
  .footer-links span { margin: 0 4px; color: #888; }
  .social { position: absolute; top: 24px; left: 646px; display: flex; gap: 6px; }
  .social i { width: 26px; height: 26px; border-radius: 50%; display: block; }
  .copyright { position: absolute; top: 76px; left: 88px; font-size: 9px; color: #8a8a8a; }
</style>
</head>
<body>
  <header class="site-header">
    <div class="brand"><span class="brand-dot"></span><span class="brand-name">Bramblewood Joinery</span></div>
    <p class="tagline">Kansas City's Premier Custom Kitchen<br>Cabinet Design Company</p>
  </header>

  <nav class="main-nav">
    <ul>
      <li class="active">Home</li>
      <li>Who We Are</li>
      <li>Getting Started</li>
      <li>Contact Us</li>
      <li>Customer Experience</li>
      <li>Professional</li>
      <li>Portfolio</li>
      <li>Cabinet Hardware</li>
    </ul>
  </nav>

  <section class="slider">
    <div class="slide-main" role="img" aria-label="Photo of a white custom kitchen with cabinets and drawers">
      <svg class="slide-arrow prev" width="14" height="24" viewBox="0 0 14 24"><path d="M11 3 L3 12 L11 21" fill="none" stroke="#fff" stroke-width="3"/></svg>
      <svg class="slide-arrow next" width="14" height="24" viewBox="0 0 14 24"><path d="M3 3 L11 12 L3 21" fill="none" stroke="#fff" stroke-width="3"/></svg>
      <p class="slide-caption">Inovative Drawer Functions</p>
    </div>
    <div class="slide-thumbs">
      <div class="slide-thumb" role="img" aria-label="Kitchen project thumbnail"></div>
      <div class="slide-thumb" role="img" aria-label="Cabinet detail thumbnail"></div>
      <div class="slide-thumb" role="img" aria-label="Kitchen island thumbnail"></div>
    </div>
  </section>

  <h2 class="section-title welcome-title">Welcome to Our Site</h2>
  <p class="welcome-text">At Bramblewood Joinery, we've been designing and building the Midwest's finest custom cabinets and fixtures for decades. From single cabinets to room remodels to entire home installations, our expert craftsmen help turn the house you live in into the home you have always dreamed of.</p>
  <div class="btn btn-read">Read More</div>

  <div class="rule rule-one"></div>

  <p class="offer-title">We are a custom cabinet company, but also create bathroom, living room, bar and entertainment and bedroom cabinets too.</p>
  <div class="gallery">
    <div class="gallery-item" role="img" aria-label="Bathroom cabinet project"></div>
    <div class="gallery-item" role="img" aria-label="Living room cabinet project"></div>
    <div class="gallery-item" role="img" aria-label="Bar cabinet project"></div>
    <div class="gallery-item" role="img" aria-label="Entertainment cabinet project"></div>
    <div class="gallery-item" role="img" aria-label="Bedroom cabinet project"></div>
  </div>

  <div class="rule rule-two"></div>

  <h2 class="section-title video-title">Featured Video</h2>
  <div class="video-intro">
    <h3>Neque porro quisquam est qui dolorem ipsum</h3>
    <p>Sed ut perspiciatis unde omnis iste natus error sit voluptatem accusantium doloremque laudantium, totam rem aperiam, eaque ipsa quae ab illo inventore veritatis et quasi architecto beatae vitae dicta sunt explicabo.</p>
  </div>
  <div class="btn btn-view">View More</div>
  <div class="video-frame" role="img" aria-label="Video still of a finished custom kitchen">
    <svg class="play-icon" width="44" height="44" viewBox="0 0 44 44"><circle cx="22" cy="22" r="20" fill="rgba(0,0,0,0.45)"/><path d="M17 13 L32 22 L17 31 Z" fill="#fff"/></svg>
  </div>

  <footer class="site-footer">
    <p class="footer-links">Home<span>|</span>Who We Are<span>|</span>Getting Started<span>|</span>Contact Us<span>|</span>Customer Experience<span>|</span>Professional<br>Portfolio<span>|</span>Cabinet Hardware</p>
    <div class="social">
      <i style="background:#3b5998"></i>
      <i style="background:#29a9e1"></i>
      <i style="background:#5aa83a"></i>
      <i style="background:#d6392b"></i>
      <i style="background:#ef7a1a"></i>
    </div>
    <p class="copyright">© 2014 Bramblewood Joinery</p>
  </footer>
</body>
</html>
```